Sleek modern site for stage hypnotist who does high school, college, university and corporate gigs.

Need a website design for stage hypnotist Gareth Munroe
I'm using a weebly domain

Gareth Munroe is a stage hypnotist who does high school shows , colleges, corporate and fundraisers
Looking for something sleek and modern looking.
I need about 4 pages at least one main describing what i do
1st page Describes what events i do (high school, college, corporate, weddings, fundraisers, fairs)
2nd page would be an about/bio page
3rd FAQ page about hypnosis.

*what venues do you work with?
*how long is your show?
*How do we promote the show?
*is it safe
*are you insured?
*how much does it cost?
4th page will be a contact page and link to my social media like Instagram, twitter, and possibly Facebook.

Included is a few pictures that I'll probably including on the site. I'm waiting on the rest for photoshoot at the this week. Some of these pictures probably will have different stock backgrounds other than grey (something like a las vegas strip or a stage.

Visually I'm looking for a cool color scheme.

Target Market(s)

High school for now but college and corporate down the road.

Industry/Entity Type

Entertainment Industry

Coding

Coded - Design and coding required

Number of Pages Required

4 page

Font styles to use
Serif
Sans Serif

Colors
3277b5
85acd3
9d9d9d
5c5c5c
cbcbcb
aaaaaa
1b1b1b
333333

Requirements
Must have
• MUST BE ABLE TO WORK WITH WEEBLY
• A sleek and professional look as if I've been doing this for years.
• The ability to edit the text of the site so i can improve upon the persuasive parts if need be.
• I also will be getting more promotional photos in the 5 or 6 days after the deadline days so if i pick your project i'd like to be able to integrate some of them into the design. The 3 photos i provided are somewhat place holders to give you an idea of the rest that are to come.
Nice to have
• drop down links
Should not have
• if you google other stage hypnotists their sites are a bit stale and not that modern.

```html
<!DOCTYPE html>
<html lang="en">
<head>
<meta charset="utf-8">
<title>Gareth Munroe — Stage Hypnotist</title>
<link href="https://fonts.googleapis.com/css2?family=Poppins:ital,wght@0,400;0,500;0,600;0,700;1,400;1,600&family=Great+Vibes&family=Open+Sans:wght@400&display=swap" rel="stylesheet">
<style>
:root{
  --ink-900:#1b1b1b;
  --ink-800:#222222;
  --ink-700:#2a2a2a;
  --ink-600:#333333;
  --grey-500:#5c5c5c;
  --grey-300:#aaaaaa;
  --grey-200:#cbcbcb;
  --white:#ffffff;
  --bronze:#b0814e;
  --text-dark:#2b2b2b;
}
*{box-sizing:border-box;margin:0;padding:0}
html,body{width:1200px;height:3061px;overflow:hidden;background:var(--white)}
body{position:relative;font-family:"Poppins",Arial,sans-serif;color:var(--white)}
.abs{position:absolute}

/* Hero */
.hero{left:0;top:0;width:1200px;height:650px;background:linear-gradient(90deg,#1d1d1d 0%,#262626 55%,#202020 100%)}
.hero-photo{left:560px;top:0;width:540px;height:650px;background:radial-gradient(ellipse at 45% 40%,#3a3a3a 0%,#262626 55%,rgba(32,32,32,0) 80%)}
.menu-btn{left:1060px;top:37px;width:40px;height:40px;border-radius:50%;background:#6d6d6d}
.menu-btn span{position:absolute;left:13px;width:14px;height:2px;background:var(--white)}
.hero-title{left:98px;top:228px;font-size:46px;font-weight:700;letter-spacing:1px}
.hero-text{left:98px;top:298px;width:410px;font-size:14px;line-height:28px;color:#e6e6e6}
.btn-outline{left:98px;top:406px;width:118px;height:38px;border:2px solid var(--white);font-size:13px;font-weight:500;display:flex;align-items:center;justify-content:center;letter-spacing:.5px}

/* About */
.about{left:0;top:650px;width:1200px;height:570px;background:var(--ink-700)}
.section-title{width:1200px;left:0;text-align:center;font-size:40px;font-weight:600}
.connector{width:2px;background:var(--white)}
.dot{width:10px;height:10px;border-radius:50%;background:var(--white)}
.about-text{left:170px;top:880px;width:860px;text-align:center;font-size:13px;line-height:30px;color:#e0e0e0}
.signature{font-family:"Great Vibes",cursive;font-size:42px;text-align:center;width:1200px;left:0}

/* What I do */
.services-bg{left:0;top:1220px;width:1200px;height:560px}
.eyebrow{left:135px;top:1232px;font-size:48px;font-weight:700;color:#3a3a3a;letter-spacing:2px}
.services-title{left:135px;top:1278px;font-size:50px;font-weight:600}
.services-text{left:98px;top:1382px;width:400px;font-size:14px;line-height:29px;color:#e6e6e6}
.event-list{left:98px;top:1488px;list-style:none;font-size:13px;line-height:29px;color:#e6e6e6}
.tile{width:294px;height:247px;display:flex;align-items:center;justify-content:center;padding-top:60px;font-size:21px;font-weight:600;background:linear-gradient(160deg,#b8956a 0%,#9e7a51 100%)}

/* Testimonials */
.testimonial-title{color:var(--ink-900);font-weight:500}
.avatar{left:530px;top:2022px;width:140px;height:140px;border-radius:50%;background:radial-gradient(circle at 50% 40%,#c9d2dc 0%,#8fa0b3 60%,#5c6f85 100%);border:5px solid #e7e7e7}
.quote-mark{font-size:70px;font-weight:700;color:var(--ink-900);line-height:1}
.testimonial-text{left:170px;top:2188px;width:860px;text-align:center;font-size:13px;font-style:italic;line-height:27px;color:var(--text-dark)}
.testimonial-author{left:0;width:1200px;top:2286px;text-align:center;font-size:15px;font-style:italic;color:var(--text-dark)}
.testimonial-author b{font-weight:600}

/* Newsletter */
.newsletter{left:0;top:2377px;width:1200px;height:473px;background:linear-gradient(180deg,#3f3f3f 0%,#2d2a27 45%,#3a312a 100%)}
.newsletter-title{left:0;width:1200px;top:2578px;text-align:center;font-size:28px;font-weight:700;letter-spacing:1px}
.signup{left:350px;top:2650px;width:500px;height:42px;display:flex;border-radius:21px;overflow:hidden}
.signup-input{flex:1;background:var(--white);color:#777;font-family:"Open Sans",Arial,sans-serif;font-size:12px;display:flex;align-items:center;padding-left:28px}
.signup-btn{width:126px;background:var(--bronze);font-size:12px;font-weight:500;display:flex;align-items:center;justify-content:center}

/* Footer */
.footer{left:0;top:2850px;width:1200px;height:211px;background:var(--ink-800)}
.footer-nav{left:0;width:1200px;top:2898px;display:flex;justify-content:center;gap:22px;font-size:13px;font-weight:500;letter-spacing:.5px}
.footer-nav .sep{color:var(--grey-200)}
.copyright{left:0;width:1200px;top:2940px;text-align:center;font-size:13px;color:#e3e3e3}
.social{left:0;width:1200px;top:2988px;display:flex;justify-content:center;gap:7px}
.social a{display:block;width:30px;height:30px;border-radius:50%;background:var(--white)}
</style>
</head>
<body>

<!-- Hero -->
<header class="abs hero"></header>
<div class="abs hero-photo" role="img" aria-label="Portrait of the hypnotist in a black shirt and glasses on a dark grey backdrop"></div>
<div class="abs menu-btn" aria-label="Menu"><span style="top:14px"></span><span style="top:19px"></span><span style="top:24px"></span></div>
<h1 class="abs hero-title">GARETH MUNROE</h1>
<p class="abs hero-text">Sed ut perspiciatis unde omnis iste natus error sit voluptatem accusantium doloremque laudantium, totam rem aperiam, eaque ipsa quae ab illo inventore</p>
<a class="abs btn-outline">READ MORE</a>

<!-- About -->
<section class="abs about"></section>
<h2 class="abs section-title" style="top:704px">About Me</h2>
<div class="abs connector" style="left:599px;top:783px;height:82px"></div>
<div class="abs dot" style="left:595px;top:820px"></div>
<p class="abs about-text">Sed ut perspiciatis unde omnis iste natus error sit voluptatem accusantium doloremque laudantium, totam rem aperiam, eaque ipsa quae ab illo inventore veritatis et quasi architecto beatae vitae dicta sunt explicabo. Nemo enim ipsam voluptatem quia voluptas sit aspernatur aut odit aut fugit, sed quia consequuntur magni dolores eos qui ratione voluptatem sequi nesciunt. Neque porro quisquam est, qui dolorem ipsum quia dolor sit amet, consectetur, adipisci velit, sed quia non numquam eius modi tempora incidunt ut labore et dolore magnam aliquam quaerat voluptatem.</p>
<div class="abs signature" style="top:1078px">Gareth Munroe</div>

<!-- What I do -->
<svg class="abs services-bg" width="1200" height="560" viewBox="0 0 1200 560" aria-hidden="true">
  <rect width="1200" height="560" fill="#2a2a2a"/>
  <polygon points="1200,270 1200,560 0,560 0,548" fill="#ffffff"/>
</svg>
<div class="abs eyebrow">HYPNOTIST</div>
<div class="abs connector" style="left:102px;top:1262px;height:88px"></div>
<div class="abs dot" style="left:98px;top:1301px"></div>
<h2 class="abs services-title">WHAT I DO</h2>
<p class="abs services-text">Sed ut perspiciatis unde omnis iste natus error sit voluptatem accusantium doloremque laudantium, totam rem aperiam, eaque ipsa quae</p>
<ul class="abs event-list">
  <li>High School</li><li>College</li><li>Corporate</li><li>Weddings</li><li>Fundraisers</li><li>Fairs</li>
</ul>
<div class="abs tile" style="left:496px;top:1245px" role="img" aria-label="Group of high school students, bronze tinted">High School</div>
<div class="abs tile" style="left:806px;top:1245px" role="img" aria-label="Corporate team gathered together, bronze tinted">Corporate</div>
<div class="abs tile" style="left:496px;top:1508px" role="img" aria-label="Wedding couple, bronze tinted">Weddings</div>
<div class="abs tile" style="left:806px;top:1508px" role="img" aria-label="Ferris wheel at a fair, bronze tinted">Fairs</div>
<div class="abs connector" style="left:599px;top:1755px;height:85px;background:var(--ink-600)"></div>
<div class="abs dot" style="left:595px;top:1828px;background:var(--ink-600)"></div>

<!-- Testimonials -->
<h2 class="abs section-title testimonial-title" style="top:1930px">Customer Testimonials</h2>
<div class="abs avatar" role="img" aria-label="Customer headshot"></div>
<div class="abs quote-mark" style="left:180px;top:2128px">&ldquo;</div>
<p class="abs testimonial-text">Lorem ipsum dolor sit amet, consectetur adipiscing elit, sed do eiusmod tempor incididunt ut labore et dolore magna aliqua. Ut enim ad minim veniam, quis nostrud exercitation ullamco laboris nisi ut aliquip ex ea commodo consequat. Duis aute irure dolor in reprehenderit in voluptate velit esse cillum dolore eu fugiat nulla pariatur. Excepteur sint occaecat</p>
<p class="abs testimonial-author"><b>Alan Pryce</b> - Nemo enim ipsam voluptatem</p>
<div class="abs quote-mark" style="left:970px;top:2290px">&rdquo;</div>

<!-- Newsletter -->
<section class="abs newsletter" role="img" aria-label="Blurred close-up of hanging crystal pendulums"></section>
<div class="abs signature" style="top:2505px">Gareth Munroe</div>
<h2 class="abs newsletter-title">SIGN UP FOR NEWSLETTER</h2>
<form class="abs signup">
  <div class="signup-input">Enter your E - mail</div>
  <div class="signup-btn">SUBSCRIBE</div>
</form>

<!-- Footer -->
<footer class="abs footer"></footer>
<nav class="abs footer-nav">
  <a>HOME</a><span class="sep">/</span><a>ABOUT</a><span class="sep">/</span><a>FAQ</a><span class="sep">/</span><a>CONTACT</a>
</nav>
<p class="abs copyright">2018 © Copyrights Gareth Munroe.All Rights Reserved</p>
<div class="abs social">
  <a aria-label="Social link 1"></a><a aria-label="Social link 2"></a><a aria-label="Social link 3"></a><a aria-label="Social link 4"></a><a aria-label="Social link 5"></a>
</div>

</body>
</html>
```